Business Card - connecting 2 souls and beggining the journey of self discovery

Logo on the front
with tag line

On the back list of services and contact details

Seminars
workshops
Coaching
podcasts

Darren Whitlow
Health & Wellbeing Life Coach
0491 372 615
darren@brightcoreliving.example
brightcoreliving.example

Industry/Entity Type

Life Coaching

Contact Information for Business Card

I like the use of colour from the logo to be used. I'm not a fan of white.

Requirements
Must have
• My tagline: Every true path begins within you
Nice to have
• Use of colour that is in the mind body soul logo

```html
<!DOCTYPE html>
<html lang="en">
<head>
<meta charset="utf-8">
<title>Brightcore Living – Business Card</title>
<link rel="stylesheet" href="https://fonts.googleapis.com/css2?family=Montserrat:wght@500&family=Open+Sans:wght@400;700&display=swap">
<style>
  :root {
    --backdrop: #1f1f21;
    --card: #ffffff;
    --ink-grey: #7a7a7c;
    --ink-dark: #4a4a4c;
    --teal: #3fb3a0;
    --purple: #6e4c9c;
    --green: #7cc35a;
    --sea: #4cb58f;
    --mark: #e9826a;
  }
  * { box-sizing: border-box; margin: 0; padding: 0; }
  html, body { width: 1200px; height: 1000px; overflow: hidden; }
  body {
    background: var(--backdrop);
    font-family: "Open Sans", sans-serif;
    position: relative;
  }
  .card {
    position: absolute;
    width: 560px;
    height: 320px;
    left: 320px;
    background: var(--card);
    border-radius: 28px;
    overflow: hidden;
    box-shadow: 0 14px 30px rgba(0,0,0,.45);
  }
  .card--front { top: 120px; }
  .card--back { top: 520px; }

  .brand {
    display: flex;
    align-items: center;
    gap: 12px;
  }
  .brand__dot {
    width: 38px; height: 38px;
    border-radius: 50%;
    background: var(--mark);
    flex: none;
  }
  .brand__name {
    font-family: "Montserrat", sans-serif;
    font-weight: 500;
    color: var(--ink-grey);
    letter-spacing: -0.5px;
    white-space: nowrap;
  }

  .card--front .brand {
    position: absolute;
    left: 0; right: 0; top: 112px;
    justify-content: center;
  }
  .card--front .brand__name { font-size: 32px; }
  .tagline {
    position: absolute;
    left: 0; right: 0; bottom: 58px;
    text-align: center;
    font-size: 12px;
    letter-spacing: 4px;
    text-transform: uppercase;
    color: var(--teal);
  }

  .card--back .brand {
    position: absolute;
    left: 38px; top: 62px;
  }
  .card--back .brand__name { font-size: 24px; }

  .services {
    position: absolute;
    left: 318px; top: 26px;
    list-style: none;
    font-size: 12.5px;
    line-height: 15px;
    color: var(--ink-dark);
  }
  .services li { display: flex; align-items: center; gap: 8px; }
  .services li::before {
    content: "";
    width: 0; height: 0;
    border-left: 6px solid var(--purple);
    border-top: 4px solid transparent;
    border-bottom: 4px solid transparent;
  }
  .contact {
    position: absolute;
    left: 318px; top: 94px;
    list-style: none;
    font-size: 12.5px;
    line-height: 16px;
    color: var(--ink-dark);
  }
  .contact li { display: flex; align-items: center; gap: 8px; }
  .contact svg { width: 10px; height: 10px; flex: none; }
  .contact .web { color: var(--teal); }

  .band {
    position: absolute;
    left: 0; top: 176px;
    width: 560px; height: 108px;
    background: linear-gradient(100deg, var(--purple) 0%, #8a8a9a 22%, var(--green) 55%, var(--sea) 100%);
  }
  .holder {
    position: absolute;
    left: 40px; top: 198px;
    color: #fff;
  }
  .holder__name {
    font-weight: 700;
    font-size: 26px;
    letter-spacing: .5px;
    text-transform: uppercase;
    line-height: 30px;
  }
  .holder__role { font-size: 19px; line-height: 24px; }
</style>
</head>
<body>

<section class="card card--front" aria-label="Card front">
  <div class="brand">
    <span class="brand__dot"></span>
    <span class="brand__name">Brightcore Living</span>
  </div>
  <p class="tagline">Every true path begins within you</p>
</section>

<section class="card card--back" aria-label="Card back">
  <div class="band" aria-hidden="true"></div>

  <div class="brand">
    <span class="brand__dot"></span>
    <span class="brand__name">Brightcore Living</span>
  </div>

  <ul class="services">
    <li>Seminars</li>
    <li>Workshops</li>
    <li>Coaching</li>
    <li>Podcasts</li>
  </ul>

  <ul class="contact">
    <li>
      <svg viewBox="0 0 10 10" aria-hidden="true"><rect x="2.5" y="0.5" width="5" height="9" rx="1" fill="none" stroke="#3fb3a0" stroke-width="1"/><circle cx="5" cy="8" r=".6" fill="#3fb3a0"/></svg>
      <span>0491 372 615</span>
    </li>
    <li>
      <svg viewBox="0 0 10 10" aria-hidden="true"><rect x="0.5" y="2" width="9" height="6.5" fill="#3fb3a0"/><polyline points="0.5,2 5,6 9.5,2" fill="none" stroke="#fff" stroke-width="0.8"/></svg>
      <span>darren@brightcoreliving.example</span>
    </li>
    <li>
      <svg viewBox="0 0 10 10" aria-hidden="true"><circle cx="5" cy="5" r="4.5" fill="#3fb3a0"/><path d="M0.5 5h9M5 0.5c-2.4 2.6-2.4 6.4 0 9M5 0.5c2.4 2.6 2.4 6.4 0 9" fill="none" stroke="#fff" stroke-width="0.6"/></svg>
      <span>www.<span class="web">brightcoreliving.example</span></span>
    </li>
  </ul>

  <div class="holder">
    <p class="holder__name">Darren Whitlow</p>
    <p class="holder__role">Life Coach</p>
  </div>
</section>

</body>
</html>
```